QRV Advisors needs a web site

We need a web site for www.qrvadvisors-example.com. QRV is a mergers and acquisition consulting company that focuses our buyer and seller services on logistics companies. We help put companies together, and help with legal and financial due diligence. We want the web site to express our service and show the logistics components. We want personalized images versus pictures of trucks and airplanes.

Our new logo uses Burgandy and grey colors. Image attached. We are not in to bold, big letters...classy, artistic, low key preferred. Confidentiality, experience, professional are what we want to express on the site.

All we expect for the first part of this project is a home page, and one subpage.  We are budgeting other funds for the technical aspects of the web site

Reason: All that I'm seeing so far is trucks, forklifts and planes. We are a legal mergers and acquisitions firm that focus on logistics. I like some of the images to say logistics, but really want it say legal, financial, and putting companies together. Will pay extra for the sub page if someone can impress us with a home page.

Reason: Swamped with another project at the moment...will work on this over the weekend and provide designer feedback and select final design by Tuesday

```html
<!DOCTYPE html>
<html lang="en">
<head>
<meta charset="utf-8">
<title>QRV Advisors – About Us</title>
<link rel="stylesheet" href="https://fonts.googleapis.com/css2?family=Cinzel:wght@400;700&family=Lato:wght@400;700&family=Oswald:wght@400&display=swap">
<style>
  :root{
    --burgundy:#a3123a;
    --burgundy-dark:#7e0c2b;
    --ink:#333;
    --text:#444;
    --icon-grey:#555;
    --social-grey:#8f8f8f;
    --white:#fff;
  }
  *{box-sizing:border-box;margin:0;padding:0}
  html,body{width:1155px;height:1200px;overflow:hidden}
  body{position:relative;font-family:"Lato",sans-serif;color:var(--text);
    background:linear-gradient(#ececec 360px,#fff 420px,#fff)}
  .abs{position:absolute}

  /* Header */
  .site-header{left:0;top:0;width:1155px;height:109px;
    background:linear-gradient(#fff,#f1f1f1);border-bottom:1px solid #ddd}
  .brand{left:129px;top:34px;display:flex;align-items:center;gap:12px}
  .brand-mark{width:14px;height:14px;background:var(--burgundy)}
  .brand-name{font-weight:700;font-size:30px;color:#5a5a5a;letter-spacing:1px}
  .header-phone{left:916px;top:17px;font-size:14.5px;color:#444;display:flex;align-items:center;gap:6px}
  .main-nav{left:470px;top:76px;display:flex;align-items:center;font-size:14.5px;color:#444}
  .main-nav a{color:inherit;text-decoration:none;padding:2px 8px;margin:0 7px;position:relative}
  .main-nav a + a::before{content:"";position:absolute;left:-8px;top:1px;height:18px;border-left:1px solid #ddd}
  .main-nav a.current{background:var(--burgundy);color:#fff;border-radius:2px}

  /* Hero */
  .hero-band{left:0;top:109px;width:1155px;height:289px;
    background:linear-gradient(90deg,#9aa7b3 0%,#c9cdd0 12%,#8e7f70 60%,#d46a2a 85%,#6b5a4c 100%)}
  .hero-frame{left:126px;top:135px;width:903px;height:235px;background:#fff;padding:5px}
  .hero-photo{position:relative;width:100%;height:100%;
    background:linear-gradient(90deg,#d9d6cc 0%,#cfc9b4 35%,#c8bb8c 70%,#c6b37e 100%)}
  .hero-title{position:absolute;right:22px;top:70px;font-family:"Cinzel",serif;font-size:41px;color:#f4efe0;letter-spacing:1px}
  .hero-strap{position:absolute;left:0;right:0;bottom:0;height:40px;background:rgba(30,30,30,.88);
    font-family:"Cinzel",serif;font-size:19px;color:#fff;display:flex;align-items:center;justify-content:center;letter-spacing:.5px}

  /* Content */
  .content{left:128px;top:430px;width:614px}
  .page-title{font-family:"Cinzel",serif;font-weight:400;font-size:29px;color:#333;padding-bottom:4px;border-bottom:1px solid #bbb}
  .lead{font-size:16.5px;line-height:24.4px;color:#333;margin-top:5px;letter-spacing:.1px}
  .body-copy{font-size:12.3px;line-height:19px;color:#444;margin-top:14px}
  .checklist{display:grid;grid-template-columns:306px 300px;row-gap:8px;margin-top:12px;list-style:none;font-size:13.5px;color:#444}
  .checklist li{display:flex;align-items:center;gap:12px;padding-left:6px;height:19px}

  /* Sidebar */
  .sidebar{left:776px;top:435px;width:253px;height:464px;border:1px solid #d4d4d4;background:#fff;padding:0 13px}
  .service{display:flex;gap:12px;padding:16px 0 14px 5px;border-bottom:1px dotted #ccc;height:81px}
  .service:first-child{padding-top:27px;height:99px}
  .service-icon{flex:none;width:63px;height:63px;border-radius:50%;border:2px solid #ddd;background:#f7f7f7;
    display:flex;align-items:center;justify-content:center}
  .service-icon.active{background:var(--burgundy);border-color:var(--burgundy-dark)}
  .service h3{font-size:16.3px;font-weight:700;color:#444;line-height:16px;margin-top:2px}
  .service p{font-size:12.3px;line-height:16.5px;color:#555;margin-top:3px}
  .newsletter{margin-top:28px;padding-left:5px;border-top:1px solid #e5e5e5;padding-top:20px}
  .newsletter h3{font-size:17.5px;font-weight:700;color:#444}
  .newsletter .email{margin-top:12px;width:216px;height:27px;border:1px solid #ccc;font-size:12.3px;color:#999;padding:6px 8px;margin-left:-2px}
  .newsletter .note{font-size:12.3px;color:#444;margin-top:12px}
  .newsletter .subscribe{margin-top:9px;width:85px;height:22px;background:var(--burgundy);color:#fff;font-size:13.5px;font-weight:700;display:flex;align-items:center;justify-content:center;margin-left:-2px}

  /* Footer */
  .footer-art{left:0;top:860px;width:1155px;height:340px}
  .footer-links{left:137px;top:1096px;display:grid;grid-template-columns:145px 110px;row-gap:9px;list-style:none;font-size:12.6px;color:#fff}
  .footer-links li::before{content:"•";color:#999;margin-right:6px;font-size:10px}
  .footer-map{left:460px;top:1058px;width:230px;height:86px;border:2px solid #777;
    background:linear-gradient(135deg,#e9e3cf,#d8d2bc 55%,#a9c6e6 80%)}
  .footer-address{left:465px;top:1150px;display:flex;gap:9px;color:#fff;font-size:13px;line-height:16px}
  .cta{left:749px;top:1030px;font-family:"Oswald",sans-serif;font-size:17px;color:#fff;line-height:28px}
  .cta .row{display:flex;align-items:center;gap:7px}
  .appointment{background:linear-gradient(#fff,#ddd);color:#333;padding:0 9px;height:26px;line-height:26px;border:1px solid #aaa;font-size:16px}
  .contact-icons{left:817px;top:1112px;display:flex;gap:16px}
  .contact-icons svg{display:block}
  .copyright{left:780px;top:1170px;font-size:11px;color:#ddd}
</style>
</head>
<body>

<header class="site-header abs">
  <div class="brand abs">
    <span class="brand-name">QRV Advisors</span>
    <span class="brand-mark"></span>
  </div>
  <div class="header-phone abs">
    <svg width="14" height="14" viewBox="0 0 24 24" aria-hidden="true"><path fill="#b5122f" d="M6.6 10.8a15 15 0 0 0 6.6 6.6l2.2-2.2a1 1 0 0 1 1-.25 11.4 11.4 0 0 0 3.6.57 1 1 0 0 1 1 1V20a1 1 0 0 1-1 1A17 17 0 0 1 3 4a1 1 0 0 1 1-1h3.5a1 1 0 0 1 1 1c0 1.25.2 2.45.57 3.6a1 1 0 0 1-.25 1z"/></svg>
    555 010 2040
  </div>
  <nav class="main-nav abs">
    <a>Home</a><a class="current">About</a><a>Consulting Services</a><a>News &amp; Events</a><a>FAQ's</a><a>Contact</a>
  </nav>
</header>

<section class="hero-band abs" role="img" aria-label="Logistics scene with trucks and a dock worker"></section>
<div class="hero-frame abs">
  <div class="hero-photo" role="img" aria-label="Consultant in an office with colleagues behind">
    <div class="hero-title">About us</div>
    <div class="hero-strap">We are a legal mergers and acquisitions firm that focus on logistics.</div>
  </div>
</div>

<main class="content abs">
  <h1 class="page-title">About Us</h1>
  <p class="lead">QRV assists business owners within the logistics industry to implement growth and exit strategies. We offer business planning and merger and acquisition(M&amp;A) advisory services.</p>
  <p class="body-copy">QRV assists business owners within the logistics industry to implement growth and exit strategies. We offer business planning and merger and acquisition(M&amp;A) advisory services. QRV services are offered by industry executives with extensive M&amp;A experience.&nbsp; Your company will benefit from a unique and outside perspective from consultants that understand your business.</p>
  <p class="body-copy">QRV can help you formulate and execute your growth strategy. We take a strategic and consultative approach with our advisory services that will help you grow your business effectively.&nbsp; Since our experience and focus is only in the logistics space, you can be confident that our process will be efficient and streamlined as we help achieve your goals.</p>
  <ul class="checklist">
    <li><svg width="16" height="14" viewBox="0 0 16 14" aria-hidden="true"><path d="M1 7l5 5L15 1" fill="none" stroke="#c9556f" stroke-width="1.6"/></svg>Consectetuer adipiscing elit</li>
    <li><svg width="16" height="14" viewBox="0 0 16 14" aria-hidden="true"><path d="M1 7l5 5L15 1" fill="none" stroke="#c9556f" stroke-width="1.6"/></svg>Donsectetuer adipiscing smit elit</li>
    <li><svg width="16" height="14" viewBox="0 0 16 14" aria-hidden="true"><path d="M1 7l5 5L15 1" fill="none" stroke="#c9556f" stroke-width="1.6"/></svg>Lorem ipsum dolor nonummy</li>
    <li><svg width="16" height="14" viewBox="0 0 16 14" aria-hidden="true"><path d="M1 7l5 5L15 1" fill="none" stroke="#c9556f" stroke-width="1.6"/></svg>Consectetuer adipiscing elit</li>
    <li><svg width="16" height="14" viewBox="0 0 16 14" aria-hidden="true"><path d="M1 7l5 5L15 1" fill="none" stroke="#c9556f" stroke-width="1.6"/></svg>Donsectetuer adipiscing smit elit</li>
    <li><svg width="16" height="14" viewBox="0 0 16 14" aria-hidden="true"><path d="M1 7l5 5L15 1" fill="none" stroke="#c9556f" stroke-width="1.6"/></svg>Lorem ipsum dolor nonummy</li>
    <li><svg width="16" height="14" viewBox="0 0 16 14" aria-hidden="true"><path d="M1 7l5 5L15 1" fill="none" stroke="#c9556f" stroke-width="1.6"/></svg>Dollar coectetuer adipiscing elit</li>
    <li><svg width="16" height="14" viewBox="0 0 16 14" aria-hidden="true"><path d="M1 7l5 5L15 1" fill="none" stroke="#c9556f" stroke-width="1.6"/></svg>Dollar coectetuer adipiscing elit</li>
  </ul>
</main>

<aside class="sidebar abs">
  <div class="service">
    <span class="service-icon active">
      <svg width="36" height="34" viewBox="0 0 36 34" aria-hidden="true">
        <rect x="2" y="5" width="24" height="22" rx="2" fill="none" stroke="#fff" stroke-width="2"/>
        <line x1="2" y1="11" x2="26" y2="11" stroke="#fff" stroke-width="2"/>
        <line x1="8" y1="2" x2="8" y2="7" stroke="#fff" stroke-width="2"/>
        <line x1="20" y1="2" x2="20" y2="7" stroke="#fff" stroke-width="2"/>
        <g fill="#fff"><rect x="6" y="14" width="3" height="3"/><rect x="12" y="14" width="3" height="3"/><rect x="6" y="20" width="3" height="3"/><rect x="12" y="20" width="3" height="3"/></g>
        <circle cx="26" cy="24" r="8" fill="#fff"/>
        <path d="M26 19v5l3 2" fill="none" stroke="#a3123a" stroke-width="1.8"/>
      </svg>
    </span>
    <div><h3>Business Planning</h3><p>Duis autem vel eu iriurm dolor dolor vulputate.</p></div>
  </div>
  <div class="service">
    <span class="service-icon">
      <svg width="36" height="32" viewBox="0 0 36 32" aria-hidden="true">
        <circle cx="24" cy="7" r="5" fill="#555"/>
        <path d="M15 26c0-7 4-11 9-11s9 4 9 11z" fill="#555"/>
        <rect x="2" y="15" width="18" height="13" fill="#fff" stroke="#555" stroke-width="2"/>
        <g fill="#555"><rect x="6" y="21" width="2" height="5"/><rect x="10" y="19" width="2" height="7"/><rect x="14" y="22" width="2" height="4"/></g>
        <line x1="0" y1="30" x2="36" y2="30" stroke="#555" stroke-width="2"/>
      </svg>
    </span>
    <div><h3>Business Merger</h3><p>Duis autem vel eu iriurm dolor dolor vulputate.</p></div>
  </div>
  <div class="service" style="border-bottom:none">
    <span class="service-icon">
      <svg width="36" height="36" viewBox="0 0 36 36" aria-hidden="true">
        <rect x="6" y="2" width="24" height="17" fill="none" stroke="#555" stroke-width="2"/>
        <path d="M10 15l5-5 4 3 6-6" fill="none" stroke="#555" stroke-width="1.8"/>
        <line x1="18" y1="19" x2="18" y2="23" stroke="#555" stroke-width="2"/>
        <g fill="#555">
          <circle cx="7" cy="27" r="3"/><path d="M2 35c0-4 2-5 5-5s5 1 5 5z"/>
          <circle cx="18" cy="27" r="3"/><path d="M13 35c0-4 2-5 5-5s5 1 5 5z"/>
          <circle cx="29" cy="27" r="3"/><path d="M24 35c0-4 2-5 5-5s5 1 5 5z"/>
        </g>
      </svg>
    </span>
    <div><h3>Acquisition (M&amp;A) Advisory</h3><p>Duis autem vel eu iriurm dolor dolor vulputate.</p></div>
  </div>
  <div class="newsletter">
    <h3>Newsletter Signup</h3>
    <div class="email">Enter your email here</div>
    <p class="note">Signup for QRV Newsletter!</p>
    <div class="subscribe">Subscribe</div>
  </div>
</aside>

<svg class="footer-art abs" viewBox="0 0 1155 340" aria-hidden="true">
  <defs>
    <linearGradient id="wine" x1="0" y1="0" x2="1" y2="0">
      <stop offset="0" stop-color="#8a0c2c"/><stop offset=".5" stop-color="#a8103a"/><stop offset="1" stop-color="#7e0b29"/>
    </linearGradient>
    <linearGradient id="dark" x1="0" y1="0" x2="0" y2="1">
      <stop offset="0" stop-color="#4a4a4a"/><stop offset=".4" stop-color="#2a2a2a"/><stop offset="1" stop-color="#1e1e1e"/>
    </linearGradient>
  </defs>
  <path d="M0,140 C150,185 380,205 600,196 C850,180 1000,120 1155,95 L1155,340 L0,340 Z" fill="url(#dark)"/>
  <path d="M0,80 C150,150 380,178 600,170 C850,160 1000,95 1155,70 L1155,95 C1000,120 850,180 600,196 C380,205 150,185 0,140 Z" fill="#cdcdcd"/>
  <path d="M0,6 C150,120 400,150 600,145 C850,138 1000,80 1110,66 C1000,95 850,160 600,170 C380,178 150,150 0,80 Z" fill="url(#wine)"/>
</svg>

<ul class="footer-links abs">
  <li>Home</li><li>News &amp; Events</li>
  <li>About</li><li>FAQ's</li>
  <li>Consulting Services</li><li>Contact</li>
</ul>

<div class="footer-map abs" role="img" aria-label="Street map of the office location"></div>
<div class="footer-address abs">
  <svg width="18" height="28" viewBox="0 0 18 28" aria-hidden="true"><path d="M9 0a9 9 0 0 0-9 9c0 7 9 19 9 19s9-12 9-19a9 9 0 0 0-9-9zm0 12.5A3.5 3.5 0 1 1 9 5.5a3.5 3.5 0 0 1 0 7z" fill="#fff"/></svg>
  <div>QRV Advisors<br>Sanfransisco, Miami, Chicago.</div>
</div>

<div class="cta abs">
  <div class="row">Schedule Free Consultation <span class="appointment">Appointment</span></div>
  <div>Or Call Us on : (555) 010 2040</div>
</div>

<div class="contact-icons abs" role="img" aria-label="Contact links: email, phone, location, website">
  <svg width="26" height="26" viewBox="0 0 26 26" aria-hidden="true"><rect x="2" y="6" width="22" height="15" fill="none" stroke="#8f8f8f" stroke-width="2"/><path d="M2 7l11 8 11-8" fill="none" stroke="#8f8f8f" stroke-width="2"/></svg>
  <svg width="26" height="26" viewBox="0 0 24 24" aria-hidden="true"><path fill="#8f8f8f" d="M6.6 10.8a15 15 0 0 0 6.6 6.6l2.2-2.2a1 1 0 0 1 1-.25 11.4 11.4 0 0 0 3.6.57 1 1 0 0 1 1 1V20a1 1 0 0 1-1 1A17 17 0 0 1 3 4a1 1 0 0 1 1-1h3.5a1 1 0 0 1 1 1c0 1.25.2 2.45.57 3.6a1 1 0 0 1-.25 1z"/></svg>
  <svg width="26" height="26" viewBox="0 0 18 28" aria-hidden="true"><path d="M9 0a9 9 0 0 0-9 9c0 7 9 19 9 19s9-12 9-19a9 9 0 0 0-9-9zm0 12.5A3.5 3.5 0 1 1 9 5.5a3.5 3.5 0 0 1 0 7z" fill="#8f8f8f"/></svg>
  <svg width="26" height="26" viewBox="0 0 26 26" aria-hidden="true"><g fill="none" stroke="#8f8f8f" stroke-width="2"><circle cx="13" cy="13" r="11"/><ellipse cx="13" cy="13" rx="5" ry="11"/><line x1="2" y1="13" x2="24" y2="13"/></g></svg>
</div>

<p class="copyright abs">© Copyright 2013 QRV Advisors.</p>

</body>
</html>
```